Tallon Electrical Business Card

We need a business card design for our family-run electrical contracting business based in Western Australia called 'Tallon Electrical'. We provide electrical services including residential, commercial and industrial. We aim for individual business cards to be made for all of our employees. We already have a company logo, which we require to be featured on the design. We would like simple, sleek and vibrant designs, which incorporate our logo and represent our business. We do not want anything involving too many graphics/images. We like the colours red, black, white and all shades of grey. The final design should communicate professionalism and trustworthiness.
We require the following contact information:
Name- Grant Pellow
EC 5871
Mobile number- 0455 870 219
Fax number (including area code)- (08) 9560 2831
Email adress- name@tallonelectrical.com.au
Electrical
- ITC Handel Bold

```html
<!DOCTYPE html>
<html lang="en">
<head>
<meta charset="utf-8">
<title>Tallon Electrical – Business Card</title>
<link rel="stylesheet" href="https://fonts.googleapis.com/css2?family=Open+Sans:ital,wght@0,400;0,600;0,800;1,400;1,700&display=swap">
<style>
  :root {
    --page-bg: #d9d9d9;
    --card-light: #ffffff;
    --card-light-shade: #e6e6e6;
    --card-dark: #262626;
    --accent-red: #e3151c;
    --ink-dark: #222222;
    --ink-light: #ffffff;
  }
  * { margin: 0; padding: 0; box-sizing: border-box; }
  html, body {
    width: 1200px; height: 901px; overflow: hidden;
    background: var(--page-bg);
    font-family: "Open Sans", Arial, sans-serif;
  }
  .business-card {
    position: absolute;
    left: 100px; top: 165px;
    width: 1000px; height: 571px;
    border-radius: 48px;
    overflow: hidden;
    background: linear-gradient(160deg, var(--card-light) 40%, var(--card-light-shade) 100%);
    box-shadow: 0 14px 34px rgba(0,0,0,0.25);
  }
  .card-wave { position: absolute; inset: 0; width: 100%; height: 100%; }
  .company-name {
    position: absolute;
    right: 60px; top: 88px;
    display: flex; align-items: center; gap: 18px;
  }
  .company-mark {
    width: 58px; height: 58px;
    background: var(--accent-red);
  }
  .company-wordmark {
    font-weight: 800;
    font-size: 46px;
    letter-spacing: 1px;
    color: var(--ink-dark);
    text-transform: uppercase;
  }
  .contact-list {
    position: absolute;
    left: 58px; top: 300px;
    list-style: none;
    color: var(--ink-light);
    font-size: 25px;
    line-height: 40px;
  }
  .contact-item { display: flex; align-items: center; gap: 12px; }
  .contact-icon { width: 22px; height: 22px; fill: var(--ink-light); flex: none; }
  .employee {
    position: absolute;
    right: 60px; bottom: 40px;
    text-align: right;
    color: var(--ink-light);
  }
  .employee-name { font-weight: 700; font-style: italic; font-size: 28px; line-height: 38px; }
  .employee-role { font-style: italic; font-size: 26px; line-height: 36px; }
</style>
</head>
<body>
  <section class="business-card">
    <svg class="card-wave" viewBox="0 0 1000 571" preserveAspectRatio="none" aria-hidden="true">
      <path d="M0,178 C320,200 620,385 1000,388 L1000,426 C620,432 320,222 0,192 Z" fill="var(--accent-red)"/>
      <path d="M0,200 C320,232 620,440 1000,436 L1000,571 L0,571 Z" fill="var(--card-dark)"/>
    </svg>

    <div class="company-name">
      <span class="company-mark"></span>
      <span class="company-wordmark">Tallon Electrical</span>
    </div>

    <ul class="contact-list">
      <li class="contact-item">
        <svg class="contact-icon" viewBox="0 0 24 24"><path d="M6.6 10.8a15.1 15.1 0 0 0 6.6 6.6l2.2-2.2c.3-.3.7-.4 1-.2 1.1.4 2.3.6 3.6.6.6 0 1 .4 1 1V20c0 .6-.4 1-1 1A17 17 0 0 1 3 4c0-.6.4-1 1-1h3.5c.6 0 1 .4 1 1 0 1.3.2 2.5.6 3.6.1.3 0 .7-.2 1z"/></svg>
        <span>0491 570 156</span>
      </li>
      <li class="contact-item">
        <svg class="contact-icon" viewBox="0 0 24 24"><path d="M6 2h9v6H6z M3 9h18v11H3z" /><rect x="6" y="12" width="3" height="2" fill="var(--card-dark)"/><rect x="11" y="12" width="3" height="2" fill="var(--card-dark)"/><rect x="6" y="16" width="3" height="2" fill="var(--card-dark)"/><rect x="11" y="16" width="3" height="2" fill="var(--card-dark)"/></svg>
        <span>(08) 5550 4821</span>
      </li>
      <li class="contact-item">
        <svg class="contact-icon" viewBox="0 0 24 24"><path d="M2 5h20v14H2z"/><path d="M2 5l10 8 10-8" fill="none" stroke="var(--card-dark)" stroke-width="1.6"/></svg>
        <span>name@tallonelectrical.com.au</span>
      </li>
      <li class="contact-item">
        <span>Level 18, 83 Sample Road, Exampleton</span>
      </li>
    </ul>

    <div class="employee">
      <p class="employee-name">Grant Pellow</p>
      <p class="employee-role">Consultant</p>
    </div>
  </section>
</body>
</html>
```